Ridgeline Journeys business card

please see website
www.ridgelinejourneys.comau

info needed on card
Curtis Halvey
Ph
email
Adventure Riding GPS trails

please use my logo and colours off my site

Curtis Halvey
curtis@ridgelinejourneys.com

```html
<!DOCTYPE html>
<html lang="en">
<head>
<meta charset="utf-8">
<title>Ridgeline Journeys business card</title>
<link rel="stylesheet" href="https://fonts.googleapis.com/css2?family=Arimo:wght@400;700&display=swap">
<style>
  :root {
    --page-bg: #e9e7e3;
    --card-white: #ffffff;
    --brand-yellow: #ffd400;
    --brand-grey: #727272;
    --rule-grey: #6e6e6e;
    --ink: #111111;
    --ink-soft: #2a2a2a;
  }
  html, body {
    margin: 0;
    padding: 0;
    width: 1200px;
    height: 892px;
    overflow: hidden;
    background: var(--page-bg);
    font-family: "Arimo", Arial, sans-serif;
  }
  .canvas {
    position: relative;
    width: 1200px;
    height: 892px;
  }
  .card {
    position: absolute;
    width: 620px;
    height: 354px;
    border-radius: 4px;
    overflow: hidden;
    box-shadow: 0 6px 18px rgba(0,0,0,0.18);
  }
  /* Front */
  .card-front {
    left: 70px;
    top: 470px;
    background: var(--card-white);
  }
  .front-band {
    position: absolute;
    left: 0; top: 0;
    width: 138px;
    height: 100%;
    background: var(--brand-yellow);
  }
  .front-rule {
    position: absolute;
    left: 150px; top: 0;
    width: 5px;
    height: 100%;
    background: var(--rule-grey);
  }
  .brand {
    position: absolute;
    display: flex;
    align-items: center;
    gap: 16px;
  }
  .brand-mark {
    border-radius: 50%;
    background: var(--brand-yellow);
    flex: none;
  }
  .brand-name {
    font-weight: 700;
    text-transform: uppercase;
    color: var(--ink);
    line-height: 1;
    letter-spacing: 1px;
  }
  .card-front .brand {
    left: 180px;
    top: 48px;
  }
  .card-front .brand-mark { width: 62px; height: 62px; }
  .card-front .brand-name { font-size: 36px; }
  .holder-name {
    position: absolute;
    left: 180px;
    top: 150px;
    margin: 0;
    font-size: 32px;
    font-weight: 400;
    color: var(--ink);
  }
  .contact-list {
    position: absolute;
    left: 180px;
    top: 210px;
    margin: 0;
    padding: 0;
    list-style: none;
    font-size: 18px;
    color: var(--ink-soft);
  }
  .contact-list li {
    display: flex;
    align-items: center;
    gap: 14px;
    margin-bottom: 12px;
  }
  .contact-icon { width: 18px; height: 18px; flex: none; }
  /* Back */
  .card-back {
    left: 510px;
    top: 68px;
    background: var(--brand-grey);
  }
  .card-back .brand {
    left: 50%;
    top: 50%;
    transform: translate(-50%, -50%);
    gap: 22px;
  }
  .card-back .brand-mark { width: 90px; height: 90px; }
  .card-back .brand-name { font-size: 40px; color: #1c1c1c; }
</style>
</head>
<body>
<main class="canvas">

  <section class="card card-back" aria-label="Business card back">
    <div class="brand">
      <span class="brand-mark"></span>
      <span class="brand-name">Ridgeline Journeys</span>
    </div>
  </section>

  <section class="card card-front" aria-label="Business card front">
    <div class="front-band"></div>
    <div class="front-rule"></div>
    <div class="brand">
      <span class="brand-mark"></span>
      <span class="brand-name">Ridgeline Journeys</span>
    </div>
    <h1 class="holder-name">Curtis Halvey</h1>
    <ul class="contact-list">
      <li>
        <svg class="contact-icon" viewBox="0 0 18 18" aria-hidden="true">
          <rect x="0.5" y="0.5" width="17" height="17" rx="2" fill="none" stroke="#222"/>
          <path d="M4 6.5c0-1 1-1.8 5-1.8s5 .8 5 1.8v1h-2.5v-1h-5v1H4z M5.5 9h7l1 4.5h-9z" fill="#222"/>
        </svg>
        <span>curtis@ridgelinejourneys.com</span>
      </li>
      <li>
        <svg class="contact-icon" viewBox="0 0 18 18" aria-hidden="true">
          <rect x="0.5" y="0.5" width="17" height="17" rx="2" fill="none" stroke="#222"/>
          <circle cx="9" cy="9" r="5" fill="none" stroke="#222" stroke-width="1.4"/>
          <path d="M4 9h10M9 4c-2 2.5-2 7.5 0 10M9 4c2 2.5 2 7.5 0 10" fill="none" stroke="#222" stroke-width="1"/>
        </svg>
        <span>www.ridgelinejourneys.com.au</span>
      </li>
    </ul>
  </section>

</main>
</body>
</html>
```